Q.I.V.A. The Millbrook Grand Jury Testimony

This is the cover artwork for the audio version
of the re-creation of the Millbrook Grand Jury testimony based around the killing of Tyrell Hawkins. I need a cover for the library binders. I have the template for the binder that I can send. The title of the audio is: Q.I.V.A. I would like the words Millbrook Grand Jury Testimony added in somehow with some creative graphics. I have a website with other audio covers. I also need the words: Unabridged CD format somewhere at the bottom. Can I send the binder template later?

Target Market(s)

Audiobook

Industry/Entity Type

Audio

Font styles to use
Serif

Requirements
Nice to have
• no bullets, no blood, no dead bodies, no police, no police cars, no protest, no
• violent images, no bullets
Should not have
• nice clear sleek look

```html
<!DOCTYPE html>
<html lang="en">
<head>
<meta charset="utf-8">
<title>Q.I.V.A. – Millbrook Grand Jury Testimony</title>
<link rel="stylesheet" href="https://fonts.googleapis.com/css2?family=Cinzel:wght@400;500&display=swap">
<style>
  :root {
    --ink-night: #05070b;
    --sky-deep: #0d1622;
    --sky-cloud: #1b2634;
    --copper: #c8773a;
    --copper-soft: #d88a4c;
    --street-amber: #8a4a22;
    --street-glow: #c9823e;
    --street-shadow: #2a1810;
  }
  html, body {
    margin: 0;
    padding: 0;
    width: 950px;
    height: 1200px;
    overflow: hidden;
    background: var(--ink-night);
  }
  .cover {
    position: relative;
    width: 950px;
    height: 1200px;
    overflow: hidden;
    background:
      radial-gradient(ellipse 70% 22% at 30% 6%, var(--sky-cloud) 0%, transparent 70%),
      radial-gradient(ellipse 60% 20% at 75% 14%, #162030 0%, transparent 70%),
      linear-gradient(180deg, var(--sky-deep) 0%, #080c12 35%, var(--ink-night) 100%);
    font-family: "Cinzel", "Times New Roman", serif;
  }
  .street-scene {
    position: absolute;
    left: 0;
    top: 330px;
    width: 950px;
    height: 700px;
    background:
      linear-gradient(180deg, transparent 0%, transparent 46%, rgba(255,236,210,0.55) 50%, rgba(255,236,210,0.15) 53%, transparent 58%),
      radial-gradient(ellipse 40% 30% at 72% 42%, rgba(200,210,230,0.3) 0%, transparent 70%),
      radial-gradient(ellipse 85% 55% at 45% 55%, var(--street-glow) 0%, var(--street-amber) 45%, var(--street-shadow) 85%);
    -webkit-mask-image: linear-gradient(180deg, transparent 0%, #000 20%, #000 84%, transparent 100%);
    mask-image: linear-gradient(180deg, transparent 0%, #000 20%, #000 84%, transparent 100%);
    opacity: 0.9;
  }
  .title {
    position: absolute;
    top: 80px;
    left: 0;
    width: 100%;
    margin: 0;
    text-align: center;
    font-weight: 400;
    font-size: 172px;
    line-height: 1;
    letter-spacing: 6px;
    color: var(--copper);
  }
  .title-rule {
    position: absolute;
    top: 263px;
    left: 93px;
    width: 742px;
    height: 3px;
    background: var(--copper);
  }
  .subtitle {
    position: absolute;
    top: 290px;
    left: 0;
    width: 100%;
    margin: 0;
    text-align: center;
    font-weight: 400;
    font-size: 38px;
    letter-spacing: 1.5px;
    color: var(--copper-soft);
    white-space: nowrap;
  }
  .format-note {
    position: absolute;
    top: 1112px;
    left: 0;
    width: 100%;
    margin: 0;
    text-align: center;
    font-size: 21px;
    letter-spacing: 2.5px;
    color: var(--copper);
  }
</style>
</head>
<body>
  <main class="cover">
    <div class="street-scene" role="img" aria-label="Long-exposure night street scene with blurred pedestrians crossing tram tracks and streaks of passing light"></div>
    <h1 class="title">Q.I.V.A.</h1>
    <div class="title-rule"></div>
    <h2 class="subtitle">Millbrook Grand Jury Testimony</h2>
    <p class="format-note">Unabridged CD format</p>
  </main>
</body>
</html>
```